Pinecrest Harbor Foundation Web Design

The design we need is for a WordPress blog that will be our content platform. We are a registered 501(c)3 non-profit that focuses on financially supporting the treatment of cancer patients that have been told they have no hope and there is nothing the conventional medical system can do for them. Through this wesbite we want to both rasie awareness about the treatment options plus, raise funds for treating patients. The two primary target audiences of the site are...

1. Terminally ill patients and their families to let them know that there is an option other then hospice and that we are hear to support that option.

2. People looking to help donate to a worthwhile cause that resonates with them.

The website is https://pinecrestharborfoundation.org/

See attached logo designs!!!

Target Market(s)

Cancer patients and their families

Industry/Entity Type

Foundation

Font styles to use
Sans Serif

Colors
ffffff
fbed22

Requirements
Must have
• I like this look of this site. It is clean, simple, helpful, soft. I like the flow of the pages.
• http://www.meadowsforcalm.org/
• I like the design and flow but NOT the color or boldness
• https://tvbn-youth.org/
• I like this style for a donation page.
• https://www.tumorstudyhub.org/we-are-tsh/join-the-cause/donations/one-time-donation
• with the addition of a Would you like your employer to match? button.
Nice to have
• White black and gold - but soft
• Even possibly grayscale like the site I like.

```html
<!DOCTYPE html>
<html lang="en">
<head>
<meta charset="utf-8">
<title>Pinecrest Harbor Foundation</title>
<link href="https://fonts.googleapis.com/css2?family=Roboto:wght@300;400;500;700&display=swap" rel="stylesheet">
<style>
:root{
  --gold:#ecc850;
  --gold-soft:#f3dc86;
  --ink:#5f5f5f;
  --ink-dark:#333;
  --muted:#8a8a8a;
  --panel:#f1f1f1;
  --footer:#6e6e6e;
  --footer-line:#858585;
  --white:#fff;
  --btn:#6b6b6b;
}
*{margin:0;padding:0;box-sizing:border-box}
html,body{width:1200px;height:2782px;overflow:hidden;background:var(--white)}
body{font-family:"Roboto",Arial,sans-serif;color:var(--ink);position:relative}
.abs{position:absolute}

/* hero */
.hero{left:0;top:0;width:1200px;height:658px;background:linear-gradient(100deg,#3e3e3e 0%,#7b7b7b 35%,#a7a7a7 60%,#8c8c8c 100%)}
.hero-photo{left:520px;top:0;width:680px;height:658px;background:radial-gradient(ellipse at 55% 55%,#8a4b5c 0%,#6f4450 35%,rgba(120,120,120,0) 70%)}
.brand{left:100px;top:300px;width:470px;text-align:center;color:var(--white);font-weight:400;font-size:38px;letter-spacing:1px;line-height:1.2}
.brand-mark{display:block;width:22px;height:22px;border-radius:50%;background:var(--gold);margin:0 auto 18px}
.menu{right:50px;top:20px;width:36px}
.menu span{display:block;height:4px;background:var(--white);margin-bottom:7px}
.hero-dots{left:122px;top:604px;display:flex;gap:9px}
.hero-dots span{width:9px;height:9px;border-radius:50%;background:var(--white)}
.hero-dots span.on{background:#c99}

/* intro + causes */
.soft-bg{left:0;top:658px;width:1200px;height:739px;background:linear-gradient(180deg,#fff 0%,#f6f0f2 40%,#efeaeb 70%,#fff 100%)}
.intro{left:170px;top:706px;width:860px;text-align:center;font-size:15px;font-weight:300;line-height:27px;color:var(--muted)}
.divider{left:540px;top:781px;width:120px;height:4px;background:#aaa}
.section-title{left:0;width:1200px;text-align:center;font-weight:700;font-size:34px;color:var(--ink);text-transform:uppercase}
.section-title em{font-style:normal;color:var(--gold)}
.cause{top:915px;width:316px;height:408px;background:var(--white)}
.cause.highlight{background:var(--gold)}
.cause-img{height:196px}
.progress{margin:-20px 14px 0;height:36px;border-radius:18px;background:var(--white);position:relative;box-shadow:0 1px 3px rgba(0,0,0,.12)}
.progress .track{position:absolute;left:18px;right:64px;top:16px;height:5px;background:#d8d8d8;border-radius:3px}
.progress .fill{position:absolute;left:0;top:0;width:55%;height:5px;background:var(--gold);border-radius:3px}
.progress b{position:absolute;right:16px;top:10px;font-size:12px;color:var(--ink-dark)}
.amounts{display:flex;justify-content:space-between;padding:16px 28px 0;font-size:13px;color:var(--ink-dark)}
.cause h3{font-weight:500;font-size:18px;line-height:21px;text-align:center;color:var(--ink-dark);margin:22px 40px 0}
.btn{display:inline-block;border-radius:20px;font-size:13px;color:var(--white);background:var(--btn);text-align:center}
.cause .btn{display:block;width:134px;height:34px;line-height:34px;margin:22px auto 0;background:var(--gold);color:var(--ink-dark)}
.cause.highlight .btn{background:var(--btn);color:var(--white)}

/* team */
.team{left:0;top:1397px;width:1200px;height:467px;background:var(--panel)}
.team-img{left:0;top:1397px;width:662px;height:467px;clip-path:polygon(0 0,100% 0,77% 100%,0 100%);background:linear-gradient(135deg,#c6a577 0%,#8d7a58 40%,#6c7fa0 70%,#c4b49c 100%)}
.team-copy{left:681px;top:1478px;width:420px}
.team-copy h2{font-size:34px;font-weight:500;line-height:44px;color:var(--ink);letter-spacing:1px}
.team-copy p{margin-top:32px;font-size:15px;line-height:19px;color:var(--ink)}
.team-copy .btn{margin-top:36px;width:153px;height:40px;line-height:40px;font-size:15px;font-weight:500}

/* testimonials */
.quote{top:2009px;width:438px;height:186px;background:var(--panel)}
.quote .avatar{position:absolute;left:24px;top:36px;width:94px;height:94px;border-radius:50%;background:radial-gradient(circle,#c9a184,#5b4538);border:3px solid #ddd}
.quote p{position:absolute;left:140px;top:38px;width:270px;font-size:11px;line-height:16px;color:var(--ink)}
.quote h4{position:absolute;left:140px;top:136px;font-size:11px;font-weight:700;color:var(--ink-dark)}
.t-dots{left:574px;top:2224px;display:flex;gap:7px}
.t-dots span{width:12px;height:12px;border-radius:50%;background:#888}

/* contact band */
.band{left:98px;top:2274px;width:1004px;height:97px;background:var(--gold)}
.band .phone-ico{position:absolute;left:30px;top:30px}
.band .ask{position:absolute;left:94px;top:34px;font-size:14px;line-height:16px;color:var(--btn);font-weight:500}
.band .number{position:absolute;left:212px;top:24px;font-size:34px;font-weight:400;color:var(--btn)}
.band .email{position:absolute;left:555px;top:35px;width:272px;height:34px;border-radius:17px;background:var(--white);font-size:13px;color:#888;line-height:34px;padding-left:38px}
.band .email svg{position:absolute;left:14px;top:12px}
.band .btn{position:absolute;left:845px;top:35px;width:133px;height:34px;line-height:34px}

/* footer */
.footer{left:0;top:2371px;width:1200px;height:411px;background:var(--footer);color:var(--white)}
.f-col{position:absolute;top:38px}
.f-col h5{font-size:15px;font-weight:500;letter-spacing:1px;text-transform:uppercase}
.mission{left:103px;width:290px}
.mission h5{font-size:27px;font-weight:400;letter-spacing:1px}
.mission p{margin-top:20px;font-size:13px;line-height:15px}
.links{left:562px}
.links ul{list-style:none;margin-top:22px}
.links li{display:flex;align-items:center;gap:14px;font-size:13px;height:31px}
.contact{left:874px;width:266px}
.c-item{position:relative;padding-left:34px;margin-top:26px;padding-bottom:16px;border-bottom:1px dashed var(--footer-line);font-size:13px;line-height:17px}
.c-item:last-child{border:none}
.c-item b{display:block;color:var(--gold);font-weight:500;margin-bottom:2px}
.c-item .dot{position:absolute;left:0;top:0;width:22px;height:22px;border-radius:50%;background:var(--gold)}
.c-item .dot svg{position:absolute;left:5px;top:5px}
.copy{left:0;top:2727px;width:1200px;height:55px;border-top:1px solid var(--footer-line);text-align:center;font-size:12px;line-height:55px;color:var(--white)}
</style>
</head>
<body>

<section class="abs hero">
  <div class="abs hero-photo" role="img" aria-label="Smiling woman in a burgundy cardigan and scarf, photographed against a soft grey backdrop"></div>
  <div class="abs brand"><span class="brand-mark"></span>Pinecrest Harbor Foundation</div>
  <div class="abs menu"><span></span><span></span><span></span></div>
  <div class="abs hero-dots"><span></span><span class="on"></span><span></span><span></span></div>
</section>

<div class="abs soft-bg" role="img" aria-label="Faint background photo of caring hands over a soft blanket"></div>
<p class="abs intro">We are a registered 501(c)3 non-profit that focuses on financially supporting the treatment of cancer patients that have been told they have no hope and there is nothing the conventional medical system can do for them.</p>
<div class="abs divider"></div>

<h2 class="abs section-title" style="top:834px">Featured <em>Causes</em></h2>

<article class="abs cause highlight" style="left:98px">
  <div class="cause-img" role="img" aria-label="Smiling young child undergoing treatment" style="background:linear-gradient(135deg,#7a6a55,#d8b79c 60%,#a48d78)"></div>
  <div class="progress"><div class="track"><div class="fill"></div></div><b>30%</b></div>
  <div class="amounts"><span>Raised: $300,000</span><span>Goal: $800,000</span></div>
  <h3>Neque porro quisquam est qui dolorem ipsum quia dolor sit</h3>
  <span class="btn">Donate Now</span>
</article>
<article class="abs cause" style="left:443px">
  <div class="cause-img" role="img" aria-label="Doctor talking with an elderly patient at home" style="background:linear-gradient(135deg,#8e8274,#d9d4cc 55%,#b3a99c)"></div>
  <div class="progress"><div class="track"><div class="fill"></div></div><b>30%</b></div>
  <div class="amounts"><span>Raised: $300,000</span><span>Goal: $800,000</span></div>
  <h3>Neque porro quisquam est qui dolorem ipsum quia dolor sit</h3>
  <span class="btn">Donate Now</span>
</article>
<article class="abs cause" style="left:787px">
  <div class="cause-img" role="img" aria-label="Nurse helping an elderly woman at her bedside" style="background:linear-gradient(135deg,#c9c6c2,#6e86a6 55%,#d7d2cc)"></div>
  <div class="progress"><div class="track"><div class="fill"></div></div><b>30%</b></div>
  <div class="amounts"><span>Raised: $300,000</span><span>Goal: $800,000</span></div>
  <h3>Neque porro quisquam est qui dolorem ipsum quia dolor sit</h3>
  <span class="btn">Donate Now</span>
</article>

<section class="abs team"></section>
<div class="abs team-img" role="img" aria-label="Volunteers collecting canned food into a donation box outdoors"></div>
<div class="abs team-copy">
  <h2>WE ARE<br>NONPROFIT TEAM</h2>
  <p>Lorem ipsum dolor sit amet, consectetur adipisicing elit, sed do eiusmod tempor iont incididunt ut labore et dolore magna aliqua. Ut enim ad minim veniam, quis nostrudi exercitation ullamco laboris nisi ut aliquip ex ea commodo consequat.</p>
  <span class="btn">Donate Now</span>
</div>

<h2 class="abs section-title" style="top:1915px;font-weight:500">Testimonials</h2>
<div class="abs quote" style="left:148px">
  <div class="avatar" role="img" aria-label="Portrait of a supporter"></div>
  <p>Lorem Ipsum is simply dummy text of the printing and typesetting industry. Lorem Ipsum has been the industry standard dummy text ever since the 1500s, when an unknown printer took a galley of type and scrambled</p>
  <h4>NADIA REYES</h4>
</div>
<div class="abs quote" style="left:614px">
  <div class="avatar" role="img" aria-label="Portrait of a supporter"></div>
  <p>Lorem Ipsum is simply dummy text of the printing and typesetting industry. Lorem Ipsum has been the industrystandard dummy text ever since the 1500s, wen an unknown printer took a galley of type and scrambled to make a type specimen book.</p>
  <h4>MARIN</h4>
</div>
<div class="abs t-dots"><span></span><span></span><span></span></div>

<section class="abs band">
  <svg class="phone-ico" width="36" height="36" viewBox="0 0 24 24"><path fill="#6b6b6b" d="M6.6 10.8a15.1 15.1 0 0 0 6.6 6.6l2.2-2.2c.3-.3.7-.4 1-.2 1.1.4 2.3.6 3.6.6.6 0 1 .4 1 1V20c0 .6-.4 1-1 1A17 17 0 0 1 3 4c0-.6.4-1 1-1h3.5c.6 0 1 .4 1 1 0 1.3.2 2.5.6 3.6.1.3 0 .7-.2 1z"/></svg>
  <div class="ask">DO YOU HAVE<br>A QUESTION?</div>
  <div class="number">+0123 456 789</div>
  <div class="email"><svg width="12" height="10" viewBox="0 0 12 10"><rect width="12" height="10" rx="1" fill="#999"/><path d="M0 1l6 4 6-4" stroke="#fff" fill="none"/></svg>Enter Email Id</div>
  <span class="btn">Subscribe</span>
</section>

<footer class="abs footer">
  <div class="f-col mission">
    <h5>Our Mission</h5>
    <p>Lorem ipsum dolor sit amet, consectetur adipisicing elit, sed do eiusmod tempor incid-idunt ut labore et dolore magna aliqua. Ut enim ad minim veniam.</p>
    <p>Quis nostrud exercitation ullamco laboris nisi ut aliquip ex ea commodo consequat. Duis aute irure dolor.</p>
  </div>
  <div class="f-col links">
    <h5>Quick Links</h5>
    <ul>
      <li><svg width="12" height="12" viewBox="0 0 12 12"><circle cx="6" cy="6" r="6" fill="#fff"/><path d="M5 3.5L7.5 6 5 8.5" stroke="#6e6e6e" stroke-width="1.5" fill="none"/></svg>Home</li>
      <li><svg width="12" height="12" viewBox="0 0 12 12"><circle cx="6" cy="6" r="6" fill="#fff"/><path d="M5 3.5L7.5 6 5 8.5" stroke="#6e6e6e" stroke-width="1.5" fill="none"/></svg>About</li>
      <li><svg width="12" height="12" viewBox="0 0 12 12"><circle cx="6" cy="6" r="6" fill="#fff"/><path d="M5 3.5L7.5 6 5 8.5" stroke="#6e6e6e" stroke-width="1.5" fill="none"/></svg>Causes</li>
      <li><svg width="12" height="12" viewBox="0 0 12 12"><circle cx="6" cy="6" r="6" fill="#fff"/><path d="M5 3.5L7.5 6 5 8.5" stroke="#6e6e6e" stroke-width="1.5" fill="none"/></svg>Event</li>
      <li><svg width="12" height="12" viewBox="0 0 12 12"><circle cx="6" cy="6" r="6" fill="#fff"/><path d="M5 3.5L7.5 6 5 8.5" stroke="#6e6e6e" stroke-width="1.5" fill="none"/></svg>News</li>
      <li><svg width="12" height="12" viewBox="0 0 12 12"><circle cx="6" cy="6" r="6" fill="#fff"/><path d="M5 3.5L7.5 6 5 8.5" stroke="#6e6e6e" stroke-width="1.5" fill="none"/></svg>Contact</li>
    </ul>
  </div>
  <div class="f-col contact">
    <h5>Contact Us</h5>
    <div class="c-item"><span class="dot"><svg width="12" height="12" viewBox="0 0 12 12"><path d="M6 0a4 4 0 0 0-4 4c0 3 4 8 4 8s4-5 4-8a4 4 0 0 0-4-4z" fill="#6e6e6e"/><circle cx="6" cy="4" r="1.5" fill="#ecc850"/></svg></span><b>Head Office</b>123, Main Street, Your City<br>USA 789456</div>
    <div class="c-item"><span class="dot"><svg width="12" height="12" viewBox="0 0 24 24"><path fill="#6e6e6e" d="M6.6 10.8a15.1 15.1 0 0 0 6.6 6.6l2.2-2.2c.3-.3.7-.4 1-.2 1.1.4 2.3.6 3.6.6.6 0 1 .4 1 1V20c0 .6-.4 1-1 1A17 17 0 0 1 3 4c0-.6.4-1 1-1h3.5c.6 0 1 .4 1 1 0 1.3.2 2.5.6 3.6.1.3 0 .7-.2 1z"/></svg></span><b>Phone Number</b>+123 456 7890<br>+123 456 7890</div>
    <div class="c-item"><span class="dot"><svg width="12" height="12" viewBox="0 0 12 10"><rect y="1" width="12" height="8" rx="1" fill="#6e6e6e"/><path d="M0 2l6 4 6-4" stroke="#ecc850" fill="none"/></svg></span><b>Email</b>info@sitename.com<br>www.sitename.com</div>
  </div>
</footer>
<div class="abs copy">Copyright © 2017, www.sitename.com, All Rights Reserved.</div>

</body>
</html>
```